RW Holloway LLC Business Card - Civil Engineering & Consulting Firm

We need a Business Card that is elegant, and masculine.  It is our Professional Civil Engineering & Consulting Company located in San Antonio TX (Not s construction or builder firm- no gears & no tool images please). We provide civil engineering services including  commercial site plans, grading and drainage plans, utility plans, hydraulics and hydrology, land planning, utility coordination, and other general civil engineering services related to commercial and residential development.
We have 2 existing Logos. We would like to convey reliability, strength, trustworthiness and attention to detail.  Blues and orange tones as per logo We are OK with the use of a darker blue in the mix.  We have 2 logo versions - Full Company Name Logo to go on the back of card, & Small Icon Logo for the front w/ personal Info.

Target Market(s)
Architects, Real Estate Developers, Other Strctural Engineers, Surveyers, General Contractors
Industry/Entity Type
Professional Civil Engineering
Contact Information for Business Card
Name, Position, Address, Cell & Office #, email, and company website
Font styles to use
Other font styles liked:
- Avian
Requirements
Should not have
- No Tools, No Gears, no Cranes, or Construction Equipment.

```html
<!DOCTYPE html>
<html lang="en">
<head>
<meta charset="utf-8">
<title>RW Holloway LLC – Business Card</title>
<link href="https://fonts.googleapis.com/css2?family=Montserrat:wght@300;400;700&display=swap" rel="stylesheet">
<style>
  :root {
    --bg: #b9b9bb;
    --card-light: #eeeeef;
    --facet-a: #e4e3e5;
    --facet-b: #f4f3f4;
    --facet-c: #dcdbdd;
    --orange: #e08a36;
    --blue: #74a0c6;
    --ink: #1c1c1c;
    --white: #ffffff;
  }
  * { box-sizing: border-box; margin: 0; padding: 0; }
  html, body { width: 1200px; height: 813px; overflow: hidden; }
  body {
    background: var(--bg);
    font-family: "Montserrat", sans-serif;
    display: flex;
    flex-direction: column;
    align-items: center;
    justify-content: center;
    gap: 40px;
  }
  .card {
    position: relative;
    width: 600px;
    height: 343px;
    overflow: hidden;
    box-shadow: 0 10px 24px rgba(0,0,0,0.35);
  }
  .card-front { background: var(--card-light); }
  .facets { position: absolute; inset: 0; }
  .brand-name {
    position: absolute;
    top: 62px;
    right: 46px;
    display: flex;
    align-items: center;
    gap: 10px;
    font-weight: 700;
    font-size: 22px;
    letter-spacing: 0.06em;
    color: var(--blue);
  }
  .brand-square { width: 14px; height: 14px; background: var(--orange); }
  .accent-block {
    position: absolute;
    left: 0;
    top: 168px;
    width: 20px;
    height: 34px;
    background: var(--orange);
  }
  .contact {
    position: absolute;
    left: 40px;
    top: 160px;
    color: var(--ink);
    font-size: 13px;
    line-height: 1.35;
  }
  .person-name {
    color: var(--orange);
    font-weight: 700;
    font-size: 18px;
    letter-spacing: 0.03em;
    text-transform: uppercase;
  }
  .person-title { font-size: 14px; margin-bottom: 12px; }
  .address { margin-bottom: 12px; }
  .contact-list { list-style: none; }
  .contact-list li { display: flex; align-items: center; gap: 10px; height: 19px; }
  .contact-list svg { width: 14px; height: 14px; flex: none; }
  .card-back {
    background: linear-gradient(165deg, #6f9dc3 0%, #9aa6b0 38%, #c99a6c 70%, #e3913f 100%);
    display: flex;
    align-items: center;
    justify-content: center;
  }
  .card-back .facets { opacity: 0.5; }
  .back-name {
    position: relative;
    color: var(--white);
    font-weight: 300;
    font-size: 44px;
    letter-spacing: 0.12em;
    text-transform: uppercase;
  }
</style>
</head>
<body>
  <section class="card card-front" aria-label="Card front">
    <svg class="facets" viewBox="0 0 600 343" preserveAspectRatio="none" aria-hidden="true">
      <polygon points="0,0 260,0 120,343 0,343" fill="var(--facet-a)"/>
      <polygon points="260,0 600,0 600,120 330,170" fill="var(--facet-c)" opacity="0.6"/>
      <polygon points="330,170 600,120 600,343 420,343" fill="var(--facet-b)"/>
      <polygon points="120,343 330,170 420,343" fill="var(--facet-a)" opacity="0.7"/>
    </svg>
    <div class="brand-name"><span class="brand-square"></span>RW Holloway LLC</div>
    <div class="accent-block"></div>
    <div class="contact">
      <p class="person-name">Dale Corven</p>
      <p class="person-title">Co-Founder</p>
      <p class="address">4120 N. Harlan Road<br>Suite 210 Brookfield 14</p>
      <ul class="contact-list">
        <li>
          <svg viewBox="0 0 16 16" aria-hidden="true"><path d="M3 1.5l3 3-1.6 1.8a9 9 0 0 0 5.3 5.3L11.5 10l3 3-2 2C6.5 15 1 9.5 1 3.5z" fill="var(--orange)"/></svg>
          555-014-2286
        </li>
        <li>
          <svg viewBox="0 0 16 16" aria-hidden="true"><rect x="1" y="3" width="14" height="4" rx="2" fill="var(--orange)"/><rect x="3" y="8" width="10" height="7" rx="1" fill="var(--orange)"/></svg>
          555-014-7731
        </li>
        <li>
          <svg viewBox="0 0 16 16" aria-hidden="true"><rect x="1" y="3" width="14" height="10" fill="var(--orange)"/><path d="M1 3l7 6 7-6" fill="none" stroke="var(--white)" stroke-width="1.2"/></svg>
          info@rwhollowayllc
        </li>
        <li>
          <svg viewBox="0 0 16 16" aria-hidden="true"><circle cx="8" cy="8" r="7" fill="var(--orange)"/><path d="M1 8h14M8 1c-3 4-3 10 0 14M8 1c3 4 3 10 0 14" fill="none" stroke="var(--white)" stroke-width="1"/></svg>
          www.rwhollowayllc.com
        </li>
      </ul>
    </div>
  </section>

  <section class="card card-back" aria-label="Card back">
    <svg class="facets" viewBox="0 0 600 343" preserveAspectRatio="none" aria-hidden="true">
      <polygon points="0,0 300,0 180,343 0,343" fill="#ffffff" opacity="0.08"/>
      <polygon points="300,0 600,0 600,200" fill="#ffffff" opacity="0.1"/>
      <polygon points="180,343 600,200 600,343" fill="#000000" opacity="0.04"/>
    </svg>
    <p class="back-name">RW Holloway LLC</p>
  </section>
</body>
</html>
```